$5 Quest Website Required

I am looking for someone to develop a website akin to the simplicity of www.boxlantern.example with a video in the center or a tab that permits one to "Accept the Challenge."

Incorporates our logo and is used to promote our "$5 Quest Program."

Please see attachments, but we are igniting entrepreneurial spirit among our nation's youth through this interactive and intensive program!

There should be a way to navigate to other sections of the site including:

About
Why
Request $5 Quest Packet
Success Stories
Partners
Link to Norvik Holdings
Updates

Thanks to all in advance!

Looking forward to working with you!

Good feel of what we are looking for in terms of "feel"

http://www.thebrightripple.example/

Thank you,

RB

Please make note of this website, we are going for a feel that is akin to this and less modern and professional...more abstract and interactive...but of course include space for our video:

Colors, feel, imagery, is great. Keep your formats, but bring on the feel!

Thank you all for your hard work and patience.

Thank you all for your hard work thus far.

Meanwhile, please understand that the $5 Quest is young, youthful, full of challenge and vitality, it is a competition among students from high school and universities.  The websites you have delivered are too corporate, stale, and standard.  I'm looking for something that is fresh, different, like www.thebrightripple.example.

Symbols, cartoonish, but serious, down to business and save the world one $5 bill at a time.  The logo can be used as a theme...the colors, the feel.

Video space for explanation on the $5 Quest front and center.  With leaves, $ signs, colorful colors, etc.

Visual needs to be compelling to Join the Challenge! Although Norvik Holdings and the tree is a parent company; $5 Quest is separate and Norvik Holdings should only be mentioned as a link.

PixelHarbor.example in regard to simplicity; and www.thebrightripple.example in terms of style.

Thank you,

Raphael

Like the designs that have been submitted; we are almost there.

Target Market(s)

Professors, students, teachers, parents and NGO leaders who wish to use our program as a way to inspire leadership/entrepreneurship/fundraise for their causes.

Requirements
Must have
• Place for the video, front and center
Include logo
Forsight for blogging, message, etc.
Nice to have
• Plan "buckets" to include"
Explanation Video
Two pamphlets
Contract
FAQs
Website with Blog, voting, registration, video upload, etc.
Flyer perfected
Parable...symbol of our life
Photos
Stats included
Testimonials
Organizations that have used (TKWLM, North Brook Lodge, Marlowton High)
Sponsors (Open Lantern, Copperleaf Learningfield)
Photos from events

I understand this takes coding and such, but want you to be aware of the long term vision for it!

```html
<!DOCTYPE html>
<html lang="en">
<head>
<meta charset="utf-8">
<title>$5 Quest</title>
<link rel="stylesheet" href="https://fonts.googleapis.com/css2?family=Roboto+Condensed:wght@400;700&family=Ubuntu:wght@400;500&family=Arimo:wght@400&display=swap">
<style>
  :root {
    --page: #ffffff;
    --orange: #fea800;
    --orange-light: #ffb623;
    --green: #08963a;
    --green-dark: #05742b;
    --lime: #d6e22b;
    --lime-dark: #c3cf14;
    --ink: #2c2c2c;
    --ink-soft: #4a4a4a;
  }
  * { margin: 0; padding: 0; box-sizing: border-box; }
  html, body { width: 1200px; height: 1123px; overflow: hidden; background: var(--page); }
  body { position: relative; font-family: "Arimo", Arial, sans-serif; color: var(--ink); }

  .stage { position: absolute; inset: 0; }
  .oval-art, .cycle-illustration { position: absolute; inset: 0; }

  .utility-nav {
    position: absolute; top: 26px; left: 795px;
    display: flex; align-items: center; gap: 24px;
    font-family: "Roboto Condensed", sans-serif; font-weight: 700; font-size: 16px; letter-spacing: .5px;
  }
  .utility-nav a { color: var(--ink); text-decoration: none; line-height: 28px; }
  .language-button {
    display: flex; align-items: center; gap: 10px;
    background: var(--lime); height: 28px; padding: 0 10px;
    font-size: 14px; color: var(--ink);
  }

  .brand {
    position: absolute; top: 88px; left: 0; width: 1206px;
    display: flex; justify-content: center; align-items: center; gap: 12px;
    font-family: "Ubuntu", sans-serif; font-weight: 500; font-size: 40px; color: var(--green);
  }
  .brand-dot { width: 26px; height: 26px; border-radius: 50%; background: var(--lime); }

  .main-nav {
    position: absolute; top: 240px; left: 145px; width: 913px; height: 61px;
    display: flex; justify-content: center; align-items: center; gap: 22px;
    font-family: "Roboto Condensed", sans-serif; font-weight: 700; font-size: 22px; letter-spacing: .3px;
  }
  .main-nav a { color: #ffffff; text-decoration: none; white-space: nowrap; }
  .main-nav a.is-current { color: var(--lime); }

  .welcome-title {
    position: absolute; top: 324px; left: 0; width: 1206px; text-align: center;
    font-family: "Ubuntu", sans-serif; font-weight: 500; font-size: 22px; color: #ffffff;
  }
  .welcome-title span { display: inline-block; padding: 0 6px 8px; border-bottom: 1px dashed rgba(255,255,255,.6); }
  .welcome-text {
    position: absolute; top: 368px; left: 230px; width: 746px;
    font-size: 15px; line-height: 20px; color: #3a2a00; text-align: justify;
  }

  .video-frame {
    position: absolute; top: 426px; left: 396px; width: 412px; height: 343px;
    background: #ffffff; border-radius: 4px;
    box-shadow: 0 26px 24px -18px rgba(120, 70, 0, .45);
    padding: 6px;
  }
  .video-inner {
    position: relative; width: 100%; height: 100%;
    border: 4px solid #e4e4e4;
    background: radial-gradient(circle at 50% 42%, #f1f7ef 0%, #ffffff 70%);
  }
  .play-button { position: absolute; left: 128px; top: 68px; }
  .video-label {
    position: absolute; top: 232px; width: 100%; text-align: center;
    font-family: "Roboto Condensed", sans-serif; font-weight: 700; font-size: 27px; color: #1e1e1e;
  }

  .accept-line {
    position: absolute; top: 845px; left: 237px; width: 720px; border-top: 2px dashed #1c1c1c;
  }
  .accept-button {
    position: absolute; top: 815px; left: 402px; width: 398px; height: 63px;
    display: flex; align-items: center; justify-content: center;
    font-family: "Ubuntu", sans-serif; font-size: 27px; color: var(--ink-soft);
    text-decoration: none;
  }
  .accept-button svg { position: absolute; inset: 0; }
  .accept-button span { position: relative; }

  .footer-brand {
    position: absolute; top: 956px; left: 0; width: 1206px;
    display: flex; justify-content: center; align-items: center; gap: 8px;
    font-family: "Ubuntu", sans-serif; font-weight: 500; font-size: 27px; color: var(--green);
  }
  .footer-brand .brand-dot { width: 16px; height: 16px; }
  .footer-note {
    position: absolute; top: 1016px; left: 0; width: 1206px; text-align: center;
    font-size: 14px; color: var(--ink);
  }
</style>
</head>
<body>
<div class="stage">
  <svg class="oval-art" width="1200" height="1123" viewBox="0 0 1200 1123" aria-hidden="true">
    <defs>
      <clipPath id="oval-clip"><ellipse cx="603" cy="547" rx="416" ry="522"/></clipPath>
      <filter id="oval-shadow" x="-10%" y="-10%" width="120%" height="120%">
        <feGaussianBlur stdDeviation="3"/>
      </filter>
    </defs>
    <ellipse cx="603" cy="549" rx="417" ry="523" fill="#bdb8ad" filter="url(#oval-shadow)"/>
    <ellipse cx="603" cy="547" rx="416" ry="522" fill="#ffffff"/>
    <g clip-path="url(#oval-clip)">
      <rect x="150" y="290" width="900" height="638" fill="var(--orange)"/>
      <line x1="150" y1="929" x2="1050" y2="929" stroke="#e6e2da" stroke-width="2" stroke-dasharray="2 2"/>
    </g>
  </svg>

  <svg class="cycle-illustration" width="1200" height="1123" viewBox="0 0 1200 1123" role="img" aria-label="Faint background illustration of a cycle linking idea, challenge, execution and reward">
    <defs>
      <clipPath id="band-clip"><ellipse cx="603" cy="547" rx="416" ry="522"/></clipPath>
      <radialGradient id="cycle-glow" cx="50%" cy="55%" r="55%">
        <stop offset="0" stop-color="var(--orange)" stop-opacity="0"/>
        <stop offset=".7" stop-color="var(--orange-light)" stop-opacity=".55"/>
        <stop offset="1" stop-color="var(--orange)" stop-opacity="0"/>
      </radialGradient>
    </defs>
    <rect x="150" y="300" width="900" height="628" fill="url(#cycle-glow)" clip-path="url(#band-clip)"/>
  </svg>

  <svg class="oval-art" width="1200" height="1123" viewBox="0 0 1200 1123" aria-hidden="true">
    <polygon points="145,240 1058,240 1040,270 1058,301 145,301 163,270" fill="var(--green)"/>
    <polygon points="163,246 1040,246 1028,270 1040,295 163,295 175,270" fill="none" stroke="var(--green-dark)" stroke-width="1"/>
  </svg>

  <nav class="utility-nav">
    <a href="#">FAQ</a>
    <a href="#">SIGNIN</a>
    <a href="#" class="language-button">LANGUAGE
      <svg width="12" height="9" viewBox="0 0 12 9"><polygon points="0,0 12,0 6,9" fill="#2c2c2c"/></svg>
    </a>
  </nav>

  <div class="brand"><span class="brand-dot"></span>$5 Quest</div>

  <nav class="main-nav">
    <a href="#" class="is-current">HOME</a>
    <a href="#">ABOUT US</a>
    <a href="#">WHY WE ARE?</a>
    <a href="#">SUCCESS STORIES</a>
    <a href="#">PARTNERS</a>
    <a href="#">NORVIK HOLDINGS</a>
  </nav>

  <h1 class="welcome-title"><span>WELCOME TO $5 QUEST</span></h1>
  <p class="welcome-text">Lorem ipsum dolor sit amet, consectetur adipiscing elit. Curabitur eu nisl odio. Cras egestas turpis in mi feugiat vel tincidunt arcu accumsan. Phasellus non posuere eros. Aenean consectetur.</p>

  <div class="video-frame">
    <div class="video-inner">
      <svg class="play-button" width="136" height="136" viewBox="0 0 136 136">
        <defs>
          <linearGradient id="play-fill" x1="0" y1="0" x2="0" y2="1">
            <stop offset="0" stop-color="#0c0c0c"/>
            <stop offset="1" stop-color="#4a4a4a"/>
          </linearGradient>
        </defs>
        <circle cx="68" cy="68" r="68" fill="url(#play-fill)"/>
        <polygon points="56,42 56,94 93,68" fill="#ffffff"/>
      </svg>
      <div class="video-label">WATCH VIDEO</div>
    </div>
  </div>

  <div class="accept-line"></div>
  <a href="#" class="accept-button">
    <svg width="398" height="63" viewBox="0 0 398 63">
      <polygon points="0,0 398,0 382,31.5 398,63 0,63 16,31.5" fill="var(--lime)"/>
      <polygon points="14,6 384,6 372,31.5 384,57 14,57 26,31.5" fill="none" stroke="var(--lime-dark)" stroke-width="2"/>
    </svg>
    <span>ACCEPT THE CHALLENGE</span>
  </a>

  <div class="footer-brand"><span class="brand-dot"></span>$5 Quest</div>
  <p class="footer-note">All Rights reserved @ $5quest</p>
</div>
</body>
</html>
```